Fitness Equipment & Service

I want to make the card eye catching and fun. We are called Corvane Motion Limited and we are based in Wales. We sell, install and service all types of fitness equipment from Skipping ropes, right through the Dumbbells, Kettle bells and Barbells through to state of the art Treadmills, Running Machines and Strength Equipment. We also design and install changing room furniture and lockers.

TYPOGRAPHY
We would like to use Futrura. Futura has an appearance of efficiency and forwardness. The typeface is derived
from simple geometric forms (near-perfect circles, triangles and squares) and is based on strokes of
near-even weight, which are low in contrast. This is most visible in the almost perfectly round stroke of
the o, which is nonetheless slightly ovoid.
The lowercase has tall ascenders, which rise above the cap line. The uppercase
characters present proportions similar to those of classical Roman capitals.

TYPOGRAPHIC CONSIDERATIONS
No Strike though
No Horizontal Scaling
No Drop Shadows
No Effects
Never use less than 120% Leading

OUR CORPORATE COLOURS
BRAND GUIDELINES
We were thinking that our primary colour palette consists of the Acid Green (Pantone 382) and Process Black.

We work closely with tquarly Ltd and would like to include their name on the card somewhere. I have attached images of the other brands that we work with as an idea or the small icons I have included that illustrate what we do?. I have very kindly been given permission to use any of the images off the files that I have included below, so I hope these help. I will include these below. I would be open to suggestions if it made the card more striking Can you do it?
Updates

Hi All, Just wanted to add a few thoughts but you are the guys with the creative visions (thats why are here) We are based in Wales, UK and we would be open to lots of different ideas on a theme but must be eye catching, Bold and FUN. If you can or think that the Welsh or any dragon could be put in there then go for it (its not a must have) We have also added some ideas for colour but again its over to you!! GO FOR IT ! Thanks and look forward to your visions! Owen

Hi All, Just thought I would sen through the contact details that need to be on the card. (if you want to play around with icons instead of the wording twitter, Facebook, go for it): Corvane Motion Limited Owen Pritchard Managing Director Mob: +44 (0)7582 913 406 e-mail: sales@corvanemotion.co.uk Web: Corvanemotion.co.uk twitter: @motionLetterbin Facebook: Corvane Motion Limited

```html
<!DOCTYPE html>
<html lang="en">
<head>
<meta charset="utf-8">
<title>Corvane Motion Limited – Business Card</title>
<link rel="stylesheet" href="https://fonts.googleapis.com/css2?family=Arimo:wght@400;700&display=swap">
<style>
  :root {
    --navy-deep: #141d4a;
    --navy: #1c2d6e;
    --blue: #2a5fae;
    --blue-bright: #3572c0;
    --gold: #c9a54a;
    --gold-light: #e2c679;
    --ink: #1a2150;
    --text-grey: #3d4250;
    --paper: #ffffff;
    --paper-shade: #eef0f2;
    --backdrop: #e7e5e1;
  }
  * { box-sizing: border-box; margin: 0; padding: 0; }
  html, body { width: 1200px; height: 950px; overflow: hidden; }
  body {
    background: var(--backdrop);
    font-family: "Arimo", Arial, sans-serif;
    position: relative;
  }
  .card {
    position: absolute;
    left: 220px;
    width: 760px;
    height: 434px;
    overflow: hidden;
    border-radius: 2px;
    box-shadow: 0 6px 18px rgba(0,0,0,0.18);
  }

  /* Back of card */
  .card-back {
    top: 28px;
    background: linear-gradient(100deg, var(--navy) 0%, var(--blue) 38%, var(--navy) 70%, var(--navy-deep) 100%);
  }
  .card-back .brand-mark {
    position: absolute;
    left: 290px; top: 80px;
    width: 180px; height: 180px;
    border-radius: 50%;
    background: radial-gradient(circle at 40% 35%, #3a63b0 0%, var(--navy-deep) 75%);
  }
  .card-back .web {
    position: absolute;
    left: 400px; top: 282px;
    color: #c8d2ea;
    font-size: 20px;
    line-height: 1.2;
    display: flex; align-items: center; gap: 12px;
  }
  .card-back .web::after {
    content: "";
    width: 70px; height: 1px;
    background: #c8d2ea;
  }

  /* Front of card */
  .card-front {
    top: 488px;
    background: linear-gradient(160deg, var(--paper) 0%, var(--paper) 55%, var(--paper-shade) 100%);
  }
  .name-band {
    position: absolute;
    left: 0; top: 70px;
    width: 560px; height: 96px;
    background: linear-gradient(90deg, var(--navy) 0%, var(--blue) 55%, var(--blue-bright) 100%);
    padding: 18px 0 0 52px;
    color: #fff;
  }
  .name-band .person { font-size: 24px; font-weight: 700; line-height: 1.2; }
  .name-band .role { font-size: 17px; line-height: 1.3; color: #e3e9f6; }
  .accent-band {
    position: absolute;
    left: 540px; top: 150px;
    width: 220px; height: 58px;
    background: linear-gradient(90deg, var(--gold) 0%, var(--gold-light) 60%, var(--gold) 100%);
  }
  .card-front .brand-mark {
    position: absolute;
    left: 470px; top: 100px;
    width: 150px; height: 150px;
    border-radius: 50%;
    background: radial-gradient(circle at 40% 35%, #3a63b0 0%, var(--navy-deep) 75%);
    border: 5px solid #d6dbe4;
  }
  .company-name {
    position: absolute;
    left: 400px; top: 268px;
    width: 320px;
    color: var(--ink);
    font-size: 20px;
    font-weight: 700;
    line-height: 1.2;
    text-align: center;
  }
  .contact-list {
    position: absolute;
    left: 52px; top: 262px;
    list-style: none;
    color: var(--text-grey);
    font-size: 17px;
    line-height: 1.45;
  }
  .contact-list .label { color: var(--ink); font-weight: 700; margin-right: 6px; }
  .address {
    position: absolute;
    right: 110px; top: 358px;
    color: var(--text-grey);
    font-size: 18px;
    line-height: 1.35;
    font-style: normal;
  }
</style>
</head>
<body>

  <section class="card card-back" aria-label="Back of business card">
    <div class="brand-mark"></div>
    <p class="web">corvanemotion.co.uk</p>
  </section>

  <section class="card card-front" aria-label="Front of business card">
    <div class="name-band">
      <p class="person">Owen Pritchard</p>
      <p class="role">Managing Director</p>
    </div>
    <div class="accent-band"></div>
    <div class="brand-mark"></div>
    <p class="company-name">Corvane Motion Limited</p>

    <ul class="contact-list">
      <li><span class="label">P :</span>+44 (0)7582 913 406</li>
      <li><span class="label">E :</span>sales@corvanemotion.co.uk</li>
      <li><span class="label">W :</span>Corvanemotion.co.uk</li>
    </ul>

    <address class="address">27 Harbour Quay<br>Penarth, CF64 1TQ</address>
  </section>

</body>
</html>
```